Business Intelligence Application - Reporting Menu and Report Criteria Design

Looking for a fresh, effective and user friendly view for the menu structure and reporting criteria screen format for a business reporting application. Initial format completed, content structure is in place, but we need the 'wow' design.. as its a serious professional report/BI tool it has to fall within certain guidelines for clarity and graphics..but we want it to be slick, friendly, great user experience. There is a large amount of complex content to fit into a small space and we need it to be very inviting, modern and intuitive.. If interested, please review the attachment. We have live screens in operation, but feel these could be improved and looking forward to seeing what great creative suggestions could be made. Please review work done to date in the attached.. We are not looking for a total re-design of everything, all the basic business content/structure is there.. but tell us what we could do to improve this in terms of graphic design... particularly the criteria screens.. thanks!
Updates

Reason: Need a few more days to review designs - thanks for all submissions so far, we will make a selection shortly.

Target Market(s)

Business analysts, hotel operations teams, finance analysts hospitality industry

Industry/Entity Type

Hospitality

Coding

Coded - Design and coding required

Number of Pages Required

4 page

Font styles to use
Sans Serif
Other font styles liked:
• Candara, please see example in deck

Colors
3276b5
3176b5
0255a3
85acd3
33a6d7
cee9f5
85cae6

Requirements
Must have
• sharp clear, logical menu structure, (currently it has 'clicks to sub-menus, we need hover over, slide to sub-menus..) colour, styling.. and most focus on revision of criteria.. right now is somewhat heavy, cumbersome.. keep colour and friendly intuitive process steps.. its heavy analytical stuff.. best of luck!
Should not have
• No grey fonts on white or grey screens! many business apps are not readable or sharp.. or fonts are too small.. colourless, so please avoid that.. see our deck - sharp dark (navy) or black fonts on white, or light shading..

```html
<!DOCTYPE html>
<html lang="en">
<head>
<meta charset="utf-8">
<title>Silver Harbor Hotels &amp; Suites – Reporting</title>
<link rel="stylesheet" href="https://fonts.googleapis.com/css2?family=Source+Sans+3:wght@400;600&display=swap">
<style>
  :root {
    --navy: #0255a3;
    --sky: #33a6d7;
    --sky-line: #5cb8e0;
    --ink: #1a1f2b;
    --white: #ffffff;
    --border: #9aa3ad;
    --dot: #3276b5;
  }
  * { box-sizing: border-box; margin: 0; padding: 0; }
  html, body { width: 1200px; height: 506px; overflow: hidden; background: var(--white); }
  body { font-family: "Source Sans 3", sans-serif; position: relative; color: var(--ink); }

  .topbar { position: absolute; left: 0; top: 0; width: 1200px; height: 60px; background: var(--navy); color: var(--white); }
  .brand { position: absolute; left: 48px; top: 15px; display: flex; align-items: center; gap: 10px; font-size: 19px; font-weight: 600; letter-spacing: -0.2px; }
  .brand-mark { width: 24px; height: 24px; border-radius: 50%; background: var(--white); }
  .welcome { position: absolute; left: 555px; top: 20px; font-size: 13px; }
  .date { position: absolute; left: 667px; top: 20px; font-size: 13px; }
  .mode-btn { position: absolute; top: 12px; width: 108px; height: 37px; background: var(--sky); color: var(--white);
    font-size: 12.5px; font-weight: 600; display: flex; align-items: center; justify-content: center; letter-spacing: .3px; }
  .mode-btn.intel { left: 832px; }
  .mode-btn.planning { left: 954px; }
  .icon { position: absolute; top: 17px; width: 26px; height: 26px; }
  .icon.bell { left: 1084px; }
  .icon.share { left: 1125px; }

  .main-nav { position: absolute; left: 48px; top: 89px; display: flex; align-items: center; font-size: 13px; font-weight: 600; }
  .main-nav span.sep { width: 3px; height: 3px; border-radius: 50%; background: var(--dot); margin: 0 9px; }

  .search { position: absolute; left: 775px; top: 81px; width: 376px; height: 37px; border: 1px solid var(--border);
    display: flex; align-items: center; justify-content: space-between; padding: 0 11px 0 15px; font-size: 12px; letter-spacing: .2px; }

  .menu { position: absolute; background: var(--sky); box-shadow: 0 3px 8px rgba(0,0,0,.18); }
  .menu-item { height: 33.5px; display: flex; align-items: center; justify-content: space-between; padding: 0 12px 0 11px;
    color: var(--white); font-size: 11.5px; border-bottom: 1px solid var(--sky-line); }
  .menu-item:last-child { border-bottom: none; }
  .menu-item.active { background: var(--navy); }
  .criteria { left: 775px; top: 142px; width: 163px; }
  .criteria::before { content: ""; position: absolute; left: 12px; top: -8px; border: 8px solid transparent; border-top: 0; border-bottom-color: var(--navy); }
  .names { left: 950px; top: 142px; width: 163px; }
  .division { left: 950px; top: 244px; width: 162px; }
  .regions { left: 967px; top: 282px; width: 163px; }
  .properties { left: 982px; top: 354px; width: 164px; }
  .properties .menu-item { padding-left: 17px; }
  .names .menu-item, .division .menu-item, .regions .menu-item { padding-left: 17px; }
  .tri-right { width: 0; height: 0; border-top: 4px solid transparent; border-bottom: 4px solid transparent; border-left: 5px solid var(--white); }
  .tri-down { width: 0; height: 0; border-left: 4.5px solid transparent; border-right: 4.5px solid transparent; border-top: 5px solid var(--white); }
</style>
</head>
<body>
  <header class="topbar">
    <div class="brand"><span class="brand-mark"></span>Silver Harbor Hotels &amp; Suites</div>
    <div class="welcome">Welcome Admin</div>
    <div class="date">Tuesday October 04.2017</div>
    <div class="mode-btn intel">INTEL</div>
    <div class="mode-btn planning">PLANNING</div>
    <svg class="icon bell" viewBox="0 0 26 26" fill="none" stroke="#fff" stroke-width="1.4" stroke-linecap="round" aria-label="Notifications">
      <path d="M8 17V11a5 5 0 0 1 10 0v6l2 2H6z"/><path d="M11 21a2 2 0 0 0 4 0"/><path d="M13 4v2"/>
      <path d="M4 9c-1 2-1 5 0 7M22 9c1 2 1 5 0 7"/>
    </svg>
    <svg class="icon share" viewBox="0 0 26 26" fill="none" stroke="#fff" stroke-width="1.4" stroke-linejoin="round" aria-label="Log out">
      <path d="M17 5l7 6-7 6v-3.5c-5 0-8 1.5-10 5 0-6 3-10 10-10.5z"/><path d="M13 9H3v13h16v-4"/>
    </svg>
  </header>

  <nav class="main-nav">
    <a>Admin</a><span class="sep"></span><a>Management</a><span class="sep"></span><a>Rooms Performance</a><span class="sep"></span>
    <a>Revenue Summary</a><span class="sep"></span><a>Demand &amp; Risk</a><span class="sep"></span><a>Inventory Analysis</a><span class="sep"></span><a>Placeholder</a>
  </nav>

  <div class="search">PROPERTY SEARCH
    <svg width="16" height="16" viewBox="0 0 16 16" fill="none" stroke="#1a1f2b" stroke-width="1.3"><circle cx="7" cy="7" r="5.3"/><path d="M11 11l4 4"/></svg>
  </div>

  <div class="menu criteria">
    <div class="menu-item active">Property Name<span class="tri-right"></span></div>
    <div class="menu-item">Property ID</div>
    <div class="menu-item">Product Type</div>
    <div class="menu-item active">All Division<span class="tri-right"></span></div>
    <div class="menu-item">All Region</div>
    <div class="menu-item">All Area</div>
  </div>

  <div class="menu names">
    <div class="menu-item">Coral</div>
    <div class="menu-item">Coral Bay Hotel</div>
  </div>

  <div class="menu division">
    <div class="menu-item" style="height:32px">North America<span class="tri-down"></span></div>
  </div>

  <div class="menu regions">
    <div class="menu-item">Southwest USA</div>
    <div class="menu-item">Northeast USA<span class="tri-down"></span></div>
  </div>

  <div class="menu properties">
    <div class="menu-item">Coral Bay Hotel</div>
    <div class="menu-item">Hudson City Hotel</div>
  </div>
</body>
</html>
```